Modern Business Card For A Digital Advertising Company

I'll be print on the Pell Prints Velour paper http://us.pellprints.com/products/velour/business-cards.html
Need's to be modern and use the color palette of the logo or gray scales. I think integrating the pixelation of the logo in to the card and having it wrap from one side to the other could be interesting. My company provides ad operations, web development, and number of other services to websites around the world. You can see my website at http://www.zantorhq.com
Contact info on the card needs to have
Owen Lasko
President
p.318.204.6637
owen@zantorhq.com
http://www.zantorhq.com
Doesn't necessarily need to be in that order
Website owners
Business

```html
<!DOCTYPE html>
<html lang="en">
<head>
<meta charset="utf-8">
<title>Zantor — Business Card</title>
<link rel="stylesheet" href="https://fonts.googleapis.com/css2?family=Open+Sans:wght@400;700;800&display=swap">
<style>
  :root {
    --backdrop: #1e1e1e;
    --card-white: #ffffff;
    --green-light: #8cc63f;
    --green-dark: #5a8a3a;
    --strip-dark: #3a3d3a;
    --ink-dark: #2f2f2f;
    --text-light: #ffffff;
  }
  * { box-sizing: border-box; margin: 0; padding: 0; }
  html, body {
    width: 1200px; height: 757px; overflow: hidden;
    background: var(--backdrop);
    font-family: "Open Sans", Arial, sans-serif;
  }
  .stage { position: relative; width: 1200px; height: 757px; }

  .card {
    position: absolute;
    width: 540px; height: 310px;
    border-radius: 26px;
    overflow: hidden;
    box-shadow: 0 12px 30px rgba(0,0,0,0.55);
  }

  /* Front */
  .card-front { left: 60px; top: 70px; background: var(--card-white); }
  .brand {
    position: absolute; left: 52px; top: 118px;
    display: flex; align-items: center; gap: 12px;
  }
  .brand-square { width: 26px; height: 26px; background: var(--green-light); }
  .brand-name {
    font-weight: 800; font-size: 36px; letter-spacing: 1px;
    color: var(--green-light);
  }
  .web-strip {
    position: absolute; left: 272px; top: 42px;
    width: 24px; height: 226px;
    background: var(--strip-dark);
  }
  .web-strip span {
    position: absolute; left: 50%; top: 50%;
    transform: translate(-50%, -50%) rotate(-90deg);
    white-space: nowrap;
    color: var(--text-light); font-weight: 700; font-size: 12px;
  }
  .contact-panel {
    position: absolute; left: 302px; top: 42px;
    width: 238px; height: 226px;
    background: linear-gradient(160deg, var(--green-dark), var(--green-light));
    color: var(--text-light);
    padding: 36px 0 0 28px;
  }
  .contact-name { font-weight: 700; font-size: 19px; letter-spacing: 0.3px; }
  .contact-title { font-size: 12px; margin: 2px 0 0 4px; }
  .contact-list { list-style: none; margin-top: 16px; font-size: 12px; }
  .contact-list li { display: flex; align-items: center; gap: 7px; margin-bottom: 3px; margin-left: 4px; }
  .contact-list svg { width: 11px; height: 11px; fill: var(--text-light); flex: none; }

  /* Back */
  .card-back {
    left: 600px; top: 380px;
    background: linear-gradient(160deg, var(--green-dark), var(--green-light));
    color: var(--text-light);
  }
  .back-brand {
    position: absolute; left: 0; right: 0; top: 92px;
    display: flex; justify-content: center; align-items: center; gap: 16px;
  }
  .back-brand .brand-square { width: 36px; height: 36px; background: var(--text-light); }
  .back-brand .brand-name { font-size: 58px; color: var(--text-light); }
  .back-web {
    position: absolute; left: 0; right: 0; top: 226px;
    text-align: center;
    font-weight: 700; font-size: 19px; letter-spacing: 1.5px;
  }
</style>
</head>
<body>
<main class="stage">
  <section class="card card-front" aria-label="Card front">
    <div class="brand">
      <span class="brand-square"></span>
      <span class="brand-name">ZANTOR</span>
    </div>
    <div class="web-strip"><span>www.zantorhq.com</span></div>
    <div class="contact-panel">
      <h1 class="contact-name">OWEN LASKO</h1>
      <p class="contact-title">President</p>
      <ul class="contact-list">
        <li>
          <svg viewBox="0 0 24 24" aria-hidden="true"><path d="M6.6 10.8a15 15 0 0 0 6.6 6.6l2.2-2.2c.3-.3.7-.4 1-.2 1.1.4 2.3.6 3.6.6.6 0 1 .4 1 1V20c0 .6-.4 1-1 1A17 17 0 0 1 3 4c0-.6.4-1 1-1h3.5c.6 0 1 .4 1 1 0 1.3.2 2.5.6 3.6.1.3 0 .7-.2 1z"/></svg>
          318.204.6637
        </li>
        <li>
          <svg viewBox="0 0 24 24" aria-hidden="true"><path d="M2 5h20v14H2z M3.5 6.5 12 13l8.5-6.5" stroke="#5a8a3a" stroke-width="1.5"/></svg>
          owen@zantorhq.com
        </li>
      </ul>
    </div>
  </section>

  <section class="card card-back" aria-label="Card back">
    <div class="back-brand">
      <span class="brand-square"></span>
      <span class="brand-name">ZANTOR</span>
    </div>
    <p class="back-web">www.zantorhq.com</p>
  </section>
</main>
</body>
</html>
```